business card deign

Logo needs the following on it.
1. attached logo
2. Tagline - "If it keeps a drink cold or the party going...we do it!"
3. Name- Dalton Pikes, Founder and CPO
4. Address - 412 E. Carver Avenue, Ste 2207, Tampa, FL. 33917
5. Phone - 555.318.4726

```html
<!DOCTYPE html>
<html lang="en">
<head>
<meta charset="UTF-8">
<title>Hopwell Business Card</title>
<link rel="stylesheet" href="https://fonts.googleapis.com/css2?family=Montserrat:wght@400;500;800&display=swap">
<style>
  :root {
    --page: #e9e6e1;
    --ink: #141414;
    --card-white: #ffffff;
    --card-black: #161616;
    --silver-light: #f2f2f2;
    --silver-mid: #7a7a7a;
    --swoosh-grey: #8c8c8c;
    --text-dark: #1a1a1a;
    --text-light: #ffffff;
  }
  html, body {
    margin: 0;
    width: 1200px;
    height: 931px;
    overflow: hidden;
    background: var(--page);
    font-family: "Montserrat", sans-serif;
  }
  .stage {
    position: relative;
    width: 1200px;
    height: 931px;
  }
  .card {
    position: absolute;
    width: 560px;
    height: 320px;
    border-radius: 4px;
    overflow: hidden;
    box-shadow: 0 10px 28px rgba(0,0,0,0.25);
  }

  /* Back side */
  .card--back {
    left: 70px;
    top: 90px;
    background: var(--card-black);
  }
  .back-pattern {
    position: absolute;
    inset: 0;
    background: linear-gradient(115deg, var(--silver-light) 0%, var(--silver-mid) 22%, #2a2a2a 45%, var(--card-black) 70%);
    opacity: 0.9;
  }
  .back-brand {
    position: absolute;
    left: 0;
    right: 0;
    top: 50%;
    transform: translateY(-50%);
    text-align: center;
    color: var(--text-light);
    font-weight: 800;
    font-size: 44px;
    letter-spacing: 14px;
    padding-left: 14px;
  }

  /* Front side */
  .card--front {
    left: 570px;
    top: 500px;
    background: var(--card-white);
  }
  .front-art {
    position: absolute;
    inset: 0;
  }
  .brand {
    position: absolute;
    left: 36px;
    top: 98px;
    display: flex;
    align-items: center;
    gap: 8px;
    color: var(--ink);
    font-weight: 800;
    font-size: 24px;
    letter-spacing: 4px;
  }
  .brand-dot {
    width: 14px;
    height: 14px;
    border-radius: 50%;
    background: var(--ink);
  }
  .divider {
    position: absolute;
    left: 262px;
    top: 46px;
    width: 1.5px;
    height: 130px;
    background: var(--ink);
  }
  .contact {
    position: absolute;
    left: 284px;
    top: 40px;
    color: var(--text-dark);
  }
  .contact-name {
    margin: 0;
    font-weight: 800;
    font-size: 20px;
    letter-spacing: 0.5px;
    text-transform: uppercase;
  }
  .contact-title {
    margin: 2px 0 16px;
    font-weight: 400;
    font-size: 15px;
  }
  .contact-row {
    display: flex;
    align-items: flex-start;
    gap: 8px;
    font-size: 14px;
    line-height: 1.3;
    margin-bottom: 3px;
  }
  .contact-row svg {
    flex: none;
    width: 14px;
    height: 14px;
    margin-top: 2px;
    fill: var(--ink);
  }
  .tagline {
    font-family: "Montserrat", sans-serif;
    font-weight: 500;
    font-size: 14px;
    fill: var(--text-light);
  }
</style>
</head>
<body>
<main class="stage">

  <section class="card card--back" aria-label="Card back">
    <div class="back-pattern" role="img" aria-label="Repeating brand mark pattern fading from silver to black"></div>
    <div class="back-brand">HOPWELL</div>
  </section>

  <section class="card card--front" aria-label="Card front">
    <svg class="front-art" viewBox="0 0 560 320" width="560" height="320">
      <defs>
        <path id="tagline-path" d="M150,313 Q380,294 548,214"/>
      </defs>
      <path d="M0,320 L0,292 Q300,292 560,185 L560,320 Z" fill="var(--card-black)"/>
      <path d="M50,282 Q330,272 540,170" fill="none" stroke="var(--swoosh-grey)" stroke-width="5" stroke-linecap="round"/>
      <text class="tagline"><textPath href="#tagline-path">If it keeps a drink cold or the party going...we do it!</textPath></text>
    </svg>

    <div class="brand"><span class="brand-dot"></span>HOPWELL</div>
    <div class="divider"></div>

    <div class="contact">
      <p class="contact-name">Dalton Pikes</p>
      <p class="contact-title">Founder and CPO</p>
      <div class="contact-row">
        <svg viewBox="0 0 24 24" aria-hidden="true"><path d="M6.6 10.8a15.1 15.1 0 0 0 6.6 6.6l2.2-2.2a1 1 0 0 1 1-.25 11.4 11.4 0 0 0 3.6.57 1 1 0 0 1 1 1V20a1 1 0 0 1-1 1A17 17 0 0 1 3 4a1 1 0 0 1 1-1h3.5a1 1 0 0 1 1 1c0 1.25.2 2.45.57 3.6a1 1 0 0 1-.25 1z"/></svg>
        <span>555.318.4726</span>
      </div>
      <div class="contact-row">
        <svg viewBox="0 0 24 24" aria-hidden="true"><path d="M12 2a7 7 0 0 0-7 7c0 5.2 7 13 7 13s7-7.8 7-13a7 7 0 0 0-7-7zm0 9.5A2.5 2.5 0 1 1 12 6.5a2.5 2.5 0 0 1 0 5z"/></svg>
        <span>412 E. Carver Avenue, Ste<br>2207, Tampa, FL. 33917</span>
      </div>
    </div>
  </section>

</main>
</body>
</html>
```